Desert Basin Company Brochure

**** UPDATE 2-8-2014 ****

Size should be 11" X 17" or larger (tri or bi fold).

We're going to let the contest run it's full duration to allow for more time spent on designs.

No black backgrounds.

Consideration should be given to having the text be easy to read and in a nice, organized format.

*****************************

We're looking for an eye-catching, colorful brochure that will explain what we do, who we are... and what sets us apart from the competition.

Our company provides swimming pool service, repair, and custom renovations throughout the Phoenix, Arizona metropolitan area. These brochures will be hand-delivered to each prospective customer we visit.

The brochure will include images of our work, product logos, and a unique design that separates our company apart from the rest.

The brochure should be tri-fold. Although, if a designer wants to (or has better ideas) for a different lay-out, then we're open to seeing what can be done.

Colors we like: Blue, White, Silver, Copper, Green (accent color)

We like designs that are unique/different. Professional. Creative. Sleek. Sexy. Custom. We don't want the brochure to be "pretentious". We'd like for these brochures to leave a lasting impression with our prospective clients... and hopefully earn us more business.

We don't want the brochure to be too wordy, however if the designer feels we need to cut back (or add), let us know.

Our motto is "Every Ripple Counts".

You can view some of our projects, and what we're about either at our website (tidewellpools.example), Facetrail (www.facebook/tidewellpools), or Searchly+ (https://plus.google.com/+Tidewellpools). Thank you!

- Print-

(Front) Logo

Service - Repair - Renovation
555-347-9180
tidewellpools.example
service@tidewellpools.example
Like Us On Facetrail! Facetrail LOGO
Searchly Plus LOGO

(Body) Why Choose Us?

Thank you for the opportunity for our company to become your pool service provider!

We’re committed to providing the best customer service possible! At the end of the day you want your pool to be clean, clear, operational, and for your service provider to be available when you need them!

We’re licensed with the Sonoran Trades Licensing Board, Bonded, and Fully Insured.
A+ reviews with the Fair Merchant Council, Corra's Picks, Brivo, Olt, Facetrail, and Searchly!
All technicians are employees... not sub-contractors! Our employees are hard working, dependable, professional, and expected to follow our strict protocol for servicing your pool.
Flat-fee service rates! Any additional equipment repairs, maintenance, or chemical implementations are directly authorized by you!
No contracts! Our Service Level Agreement Form allows you to select your desired level of authorization for equipment repairs, filter maintenance, and extra chemical implementation programs.
Our uniformed technicians arrive in distinctive, clean GPS-tracked company trucks.
We leave detailed service slips after each service visit. In addition, all service visit information is electronically recorded and stored.
Easy, online account management to view and pay invoices or authorize estimates.
Invoices, estimates, questions, pictures, and video are communicated via e-mail!
Free service calls to diagnose equipment issues outside of our normal service.
10% Service Client Discount for all repairs and replacement items.
Tidewell Pools knows the importance of communication! We’re available by phone, email, or text all days of the week.

(Body) Our Methodology

We believe in 5 important factors in maintaining a clean, clear, and operational pool...

Good, Clean Water! Our local water supply contains high amounts of minerals. Pool chemicals add to this problem in a short amount of time. Our philosophy is to use the least amount of chemicals possible to achieve optimal water balance.
Efficient Water Flow! The invention of variable-speed pumps has enabled the ability to "dial in" proper water flow... while driving down energy costs.
Proper Filtration! Today’s high-capacity cartridge filters provide great filtration, save on wasted water from backwashing sand filters, and eliminate the need for water flow-restricting backwash valves.
Functioning Cleaning System! Having a working automatic cleaning system is vital in keeping the pool surface clean of debris and dirt... and free of staining.
A Dependable And Professional Pool Maintenance Technician! Our job is to not only oversee all of the items listed above... but to make sure your pool is in the best condition possible!

(Body) Equipment Repair & Installation

We’re educated on all phases of swimming pool equipment repair and installation... with a focus on energy-efficiency and optimum performance!

We’re an VRE & MQW Authorized Installer of variable-speed pool pumps. VRE & MQW trust us to properly install and calibrate all variable-speed pumps. We've been equipped to handle the new industry standards on variable-speed pumps since Arizona law went into effect January 1st, 2011.
We’re experts at acid washes and erasing the mineral build-up off of waterlines. All work is done in-house with our customized cleaning rig and trailer.
Heating systems. New efficiency standards have made installation and operation more affordable than ever.
Remote control automation systems. Technology now allows the user to easily view and control their entire pool system via a remote home computer, tablet, or phone!
Brilliant, color-changing LED lighting for pools and spas! The benefits of LED include brighter and broader displays... while lasting much longer than your typical light bulbs.
Salt systems provide a soft-water experience! In addition to the benefit of better feeling water, salt systems generate plenty of chlorine to keep your pool sanitized.

(Body) About Us

A native to Phoenix, Daniel Harrow founded Tidewell Pools in 2000. Our company was built from the ground up by way of hard work, word of mouth, and determination. Our company will always remain firmly grounded, and continue to develop systems that put our customers first!

Our philosophy is to treat every pool as if it were our own, run an efficient and organized business, and care for our employees.

Tidewell Pools is a yearly, proud contributor to the Saguaro Youth Clinic Swim Smart Day. Please educate and watch all children around water... every accident can be avoided.

(Back) Contact Us

Office: 555-347-9180 | Fax: 555-347-9186 | Email: service@tidewellpools.example
tidewellpools.example

Office / Warehouse Location
41572 West 8th Street, Suite 4
Phoenix, Arizona 85999
(NW of 8th Street & Mesquite Ridge Road)

AZ ROC: 731150, 731151, 731152, 604378

Target Market(s)

We target a market of pool owners, which typically have more disposable income.

30 - 75 years old.

Our clients range from first-time home buyers, self-employed, business professionals, doctors, landlords, thousandaires, millionaires.

Industry/Entity Type

Pool Service

Font styles to use
Serif

Colors
0355a3
cfdfed
ffffff
3176b5
eaf1f7

Requirements
Must have
• Must use provided images. We've included a few pool pictures, and will let you decide which ones to incorporate throughout the brochure.

Logos Used:
Tidewell Pools
Hydrovel
FMC
Corra's Picks
VRE
MQW
Saguaro Youth Clinic
Searchly+
Facetrail

Image pic of some of our trucks.

Nice to have
• Equipment images worked in.
Should not have
• Cartoonish fonts or design. No "Love" hearts!!

```html
<!DOCTYPE html>
<html lang="en">
<head>
<meta charset="utf-8">
<title>Tidewell Pools – Brochure Inside Spread</title>
<link href="https://fonts.googleapis.com/css2?family=PT+Serif:wght@400;700&family=Mulish:wght@300&display=swap" rel="stylesheet">
<style>
  :root {
    --brand-blue: #0355a3;
    --mid-blue: #3176b5;
    --paper: #cfdfed;
    --paper-light: #eaf1f7;
    --white: #ffffff;
    --stone: #d9cdbb;
    --water: #a9c4d6;
  }
  html, body {
    margin: 0;
    padding: 0;
    overflow: hidden;
  }
  body {
    width: 1200px;
    height: 849px;
    background: var(--paper);
  }
  .spread {
    position: relative;
    width: 1200px;
    height: 849px;
    overflow: hidden;
    background: linear-gradient(180deg, var(--paper) 0%, #d6e3ef 100%);
    font-family: "PT Serif", Georgia, serif;
    color: var(--brand-blue);
  }
  .pool-photo {
    position: absolute;
    left: 300px;
    top: 420px;
    width: 900px;
    height: 429px;
    background:
      radial-gradient(ellipse 260px 120px at 290px 290px, #8a9a88 0%, rgba(138,154,136,0) 100%),
      radial-gradient(ellipse 420px 140px at 620px 230px, var(--stone) 0%, rgba(217,205,187,0) 100%),
      radial-gradient(ellipse 300px 90px at 800px 370px, #c9b9a1 0%, rgba(201,185,161,0) 100%),
      linear-gradient(180deg, var(--paper) 0%, var(--water) 45%, #9fb3b4 100%);
    -webkit-mask-image: linear-gradient(90deg, transparent 0%, #000 25%), linear-gradient(180deg, transparent 0%, #000 30%);
    -webkit-mask-composite: source-in;
    mask-image: linear-gradient(90deg, transparent 0%, #000 25%), linear-gradient(180deg, transparent 0%, #000 30%);
    mask-composite: intersect;
  }
  .panel {
    position: absolute;
    top: 62px;
    width: 318px;
  }
  .panel--why { left: 47px; }
  .panel--method { left: 447px; }
  .panel--equipment { left: 847px; width: 310px; }
  .panel__title {
    margin: 0 0 12px;
    font-size: 19px;
    font-weight: 700;
    line-height: 18px;
    color: var(--brand-blue);
  }
  .panel p {
    margin: 0;
    font-size: 13.3px;
    line-height: 14.4px;
  }
  .panel p + p.gap { margin-top: 14.4px; }
  .motto-band {
    position: absolute;
    left: 47px;
    top: 727px;
    width: 1153px;
    height: 61px;
    background: var(--brand-blue);
    display: flex;
    align-items: center;
  }
  .motto-band__text {
    margin: 0 0 0 25px;
    font-family: "Mulish", Arial, sans-serif;
    font-weight: 300;
    font-size: 24.5px;
    letter-spacing: 0.5px;
    color: var(--white);
    text-transform: uppercase;
  }
</style>
</head>
<body>
<main class="spread">
  <div class="pool-photo" role="img" aria-label="Photo of a misty pool with a flagstone deck and raised spa"></div>

  <section class="panel panel--why">
    <h2 class="panel__title">Why Choose Us?</h2>
    <p>Thank you for the opportunity for our company to become your pool service provider!</p>
    <p class="gap">We’re committed to providing the best customer service possible! At the end of the day you want your pool to be clean, clear, operational, and for your service provider to be available when you need them!</p>
    <p class="gap">We’re licensed with the Sonoran Trades Licensing Board, Bonded, and Fully Insured.</p>
    <p>A+ reviews with the Fair Merchant Council, Corra's Picks, Brivo, Olt, Facetrail, and Searchly!</p>
    <p>All technicians are employees... not sub-contractors! Our employees are hard working, dependable, professional, and expected to follow our strict protocol for servicing your pool.</p>
    <p>Flat-fee service rates! Any additional equipment repairs, maintenance, or chemical implementations are directly authorized by you!</p>
    <p>No contracts! Our Service Level Agreement Form allows you to select your desired level of authorization for equipment repairs, filter maintenance, and extra chemical implementation programs.</p>
    <p>Our uniformed technicians arrive in distinctive, clean GPS-tracked company trucks.</p>
    <p>We leave detailed service slips after each service visit. In addition, all service visit information is electronically recorded and stored.</p>
    <p>Easy, online account management to view and pay invoices or authorize estimates.</p>
    <p>Invoices, estimates, questions, pictures, and video are communicated via e-mail!</p>
    <p>Free service calls to diagnose equipment issues outside of our normal service.</p>
    <p>10% Service Client Discount for all repairs and replacement items.</p>
    <p>Tidewell Pools knows the importance of communication! We’re available by phone, email, or text all days of the week.</p>
  </section>

  <section class="panel panel--method">
    <h2 class="panel__title">Our Methodology</h2>
    <p>We believe in 5 important factors in maintaining a clean, clear, and operational pool...</p>
    <p class="gap">Good, Clean Water! Our local water supply contains high amounts of minerals. Pool chemicals add to this problem in a short amount of time. Our philosophy is to use the least amount of chemicals possible to achieve optimal water balance.</p>
    <p>Efficient Water Flow! The invention of variable-speed pumps has enabled the ability to "dial in" proper water flow... while driving down energy costs.</p>
    <p>Proper Filtration! Today’s high-capacity cartridge filters provide great filtration, save on wasted water from backwashing sand filters, and eliminate the need for water flow-restricting backwash valves.</p>
    <p>Functioning Cleaning System! Having a working automatic cleaning system is vital in keeping the pool surface clean of debris and dirt... and free of staining.</p>
    <p>A Dependable And Professional Pool Maintenance Technician! Our job is to not only oversee all of the items listed above... but to make sure your pool is in the best condition possible!</p>
  </section>

  <section class="panel panel--equipment">
    <h2 class="panel__title">Equipment Repair &amp;<br>Installation</h2>
    <p>We’re educated on all phases of swimming pool equipment repair and installation... with a focus on energy-efficiency and optimum performance!</p>
    <p class="gap">We’re an VRE &amp; MQW Authorized Installer of variable-speed pool pumps. VRE &amp; MQW trust us to properly install and calibrate all variable-speed pumps. We've been equipped to handle the new industry standards on variable-speed pumps since Arizona law went into effect January 1st, 2011.</p>
    <p>We’re experts at acid washes and erasing the mineral build-up off of waterlines. All work is done in-house with our customized cleaning rig and trailer.</p>
    <p>Heating systems. New efficiency standards have made installation and operation more affordable than ever.</p>
    <p>Remote control automation systems. Technology now allows the user to easily view and control their entire pool system via a remote home computer, tablet, or phone!</p>
    <p>Brilliant, color-changing LED lighting for pools and spas! The benefits of LED include brighter and broader displays... while lasting much longer than your typical light bulbs.</p>
    <p>Salt systems provide a soft-water experience! In addition to the benefit of better feeling water, salt systems generate plenty of chlorine to keep your pool sanitized.</p>
  </section>

  <div class="motto-band">
    <p class="motto-band__text">Every Ripple Counts</p>
  </div>
</main>
</body>
</html>
```